Business Card Design for Occupational Medicine Start Up Company

We need to design a professional business card. We are a healthcare company providing occupational medicine services to blue collar industries. We are professional, efficient and high quality service providers.

Target Market(s)

Blue Collar Industry: Shipbuilding, Ports, Trucking Companies; The Executives and Safety Officers for these companies

Industry/Entity Type

Healthcare

Contact Information for Business Card

Logo, Name, Title, Email, Phone

Other font styles liked:
• Please match our Brand Guide

Requirements
Must have
• Our Company Colors and Logo

```html
<!DOCTYPE html>
<html lang="en">
<head>
<meta charset="utf-8">
<title>CrewWell Clinics – Business Card</title>
<link rel="stylesheet" href="https://fonts.googleapis.com/css2?family=Montserrat:wght@300;400;700;800&family=Arimo:wght@400&display=swap">
<style>
  :root {
    --stage: #1f1f21;
    --navy: #2a3483;
    --sky: #3db4e5;
    --sky-deep: #229fd8;
    --amber: #f3b04f;
    --plum: #7a5a74;
    --white: #ffffff;
    --ink: #111111;
    --rule: #9a9a9a;
  }
  * { box-sizing: border-box; margin: 0; padding: 0; }
  html, body { width: 1200px; height: 1015px; overflow: hidden; }
  body {
    background: var(--stage);
    display: flex; flex-direction: column; align-items: center; justify-content: center;
    gap: 44px;
    font-family: "Arimo", Arial, sans-serif;
  }
  .card {
    width: 760px; height: 434px; position: relative; overflow: hidden;
    box-shadow: 0 14px 30px rgba(0,0,0,.55);
  }

  /* Front */
  .card--front {
    background: linear-gradient(to bottom, var(--sky-deep) 0%, #2450a6 22%, var(--navy) 45%, #3a3a7c 60%, var(--plum) 76%, #c08a5e 90%, #e9aa52 100%);
    color: var(--white);
    display: flex; flex-direction: column; align-items: center; justify-content: center;
  }
  .brand { display: flex; align-items: center; gap: 16px; font-family: "Montserrat", sans-serif; font-weight: 800; }
  .brand__dot { width: 58px; height: 58px; border-radius: 50%; }
  .brand__name { font-size: 50px; letter-spacing: 1px; text-transform: uppercase; line-height: 1; }
  .brand__sub { display: block; font-size: 21px; letter-spacing: 14px; margin-top: 10px; }
  .card--front .brand__dot { background: var(--white); }
  .front__web { margin-top: 58px; font-family: "Montserrat", sans-serif; font-size: 19px; letter-spacing: .5px; }

  /* Back */
  .card--back { background: var(--white); }
  .back__brand { position: absolute; left: 52px; top: 150px; color: var(--navy); }
  .back__brand .brand__dot { background: var(--navy); width: 46px; height: 46px; }
  .back__brand .brand__name { font-size: 36px; }
  .back__brand .brand__sub { font-size: 16px; letter-spacing: 10px; margin-top: 8px; }
  .divider { position: absolute; left: 400px; top: 92px; width: 1px; height: 192px; background: var(--rule); }
  .contact { position: absolute; left: 430px; top: 84px; color: var(--ink); }
  .contact__name { font-family: "Montserrat", sans-serif; font-size: 29px; color: var(--navy); line-height: 1; }
  .contact__name b { font-weight: 800; }
  .contact__name span { font-weight: 300; }
  .contact__title { font-size: 17px; margin-top: 4px; }
  .contact__list { list-style: none; margin-top: 18px; font-size: 17px; line-height: 25px; }
  .contact__list li { display: flex; align-items: center; gap: 9px; }
  .contact__list svg { width: 16px; height: 16px; fill: var(--navy); flex: none; }
  .contact__web em { font-style: normal; color: var(--navy); }
  .contact__address { margin-top: 16px; font-size: 17px; line-height: 23px; padding-left: 25px; }

  .bands { position: absolute; left: 0; right: 0; bottom: 0; height: 34px; display: flex; align-items: flex-end; gap: 5px; }
  .band--amber { background: var(--amber); width: 41%; height: 22px; }
  .band--navy { background: var(--navy); width: 36%; height: 30px; }
  .band--sky { background: var(--sky); flex: 1; height: 34px; }
</style>
</head>
<body>

<section class="card card--front" aria-label="Card front">
  <div class="brand">
    <span class="brand__dot"></span>
    <div class="brand__name">CrewWell<span class="brand__sub">Clinics</span></div>
  </div>
  <p class="front__web">www.crewwellclinics.com</p>
</section>

<section class="card card--back" aria-label="Card back">
  <div class="brand back__brand">
    <span class="brand__dot"></span>
    <div class="brand__name">CrewWell<span class="brand__sub">Clinics</span></div>
  </div>

  <div class="divider"></div>

  <div class="contact">
    <h1 class="contact__name"><b>DANIEL</b> <span>MARSH</span></h1>
    <p class="contact__title">Managing Director</p>
    <ul class="contact__list">
      <li><svg viewBox="0 0 24 24"><path d="M6.6 10.8a15.1 15.1 0 0 0 6.6 6.6l2.2-2.2a1 1 0 0 1 1-.25 11.4 11.4 0 0 0 3.6.57 1 1 0 0 1 1 1V20a1 1 0 0 1-1 1A17 17 0 0 1 3 4a1 1 0 0 1 1-1h3.5a1 1 0 0 1 1 1c0 1.25.2 2.45.57 3.57a1 1 0 0 1-.25 1z"/></svg>044-555 010 220</li>
      <li><svg viewBox="0 0 24 24"><path d="M2 5h20v14H2z M3.5 6.5 12 13l8.5-6.5" fill="none" stroke="#2a3483" stroke-width="2"/></svg>info@crewwell.com</li>
      <li class="contact__web"><svg viewBox="0 0 24 24"><circle cx="12" cy="12" r="9" fill="none" stroke="#2a3483" stroke-width="2"/><path d="M3 12h18M12 3c3 3 3 15 0 18M12 3c-3 3-3 15 0 18" fill="none" stroke="#2a3483" stroke-width="1.6"/></svg>www.<em>crewwellclinics</em>.com</li>
    </ul>
    <p class="contact__address">18, Harbour Works Road<br>45100, Portland Bay</p>
  </div>

  <div class="bands">
    <span class="band--amber"></span>
    <span class="band--navy"></span>
    <span class="band--sky"></span>
  </div>
</section>

</body>
</html>
```